Brightfield Ventures Inc. Letterhead

Creation of attractive and eye catching letterhead for a business start-up for the construction industry. Letterhead must relate to construction, but avoid standard hammer and tools in the design.

I forgot to add some details, sorry about that. Some pertinent info: Ph: 916-555-0187 brightfieldventures.example 448 Willowmere Ave, Ste 210 Folsom, CA 95999 info@brightfieldventures.example not sure if slogan should be in there" “Connecting construction professionals to create a purpose driven industry.” must be able to be used in word. Thanks!

```html
<!DOCTYPE html>
<html lang="en">
<head>
<meta charset="utf-8">
<title>Brightfield Ventures Inc. Letterhead</title>
<link href="https://fonts.googleapis.com/css2?family=Lato:wght@400;700&family=Montserrat:wght@700&family=Great+Vibes&display=swap" rel="stylesheet">
<style>
  :root {
    --navy: #1c1f5a;
    --red: #d32a2f;
    --ink: #4a4a4a;
    --paper: #ffffff;
  }
  * { margin: 0; padding: 0; box-sizing: border-box; }
  html, body { width: 914px; height: 1200px; overflow: hidden; background: var(--paper); }
  .letterhead {
    position: relative; width: 914px; height: 1200px;
    background: var(--paper); font-family: "Lato", sans-serif; color: var(--ink);
  }
  .brand {
    position: absolute; left: 64px; top: 78px;
    display: flex; align-items: center; gap: 12px;
  }
  .brand-mark { width: 22px; height: 22px; background: var(--red); }
  .brand-name {
    font-family: "Montserrat", sans-serif; font-weight: 700;
    font-size: 22px; letter-spacing: 1px; color: var(--navy);
  }
  .header-rule {
    position: absolute; top: 160px; height: 2px; background: var(--navy);
  }
  .header-rule.left { left: 0; width: 565px; }
  .header-rule.right { left: 845px; width: 69px; }
  .header-web {
    position: absolute; left: 560px; width: 285px; top: 150px;
    text-align: center; font-size: 15px; letter-spacing: 1px; color: var(--ink);
  }
  .header-web strong { color: var(--navy); font-weight: 700; }
  .letter-body { position: absolute; left: 66px; width: 780px; top: 381px; }
  .salutation { font-weight: 700; font-size: 17px; color: var(--navy); margin-bottom: 22px; }
  .letter-body p {
    font-size: 17.5px; line-height: 27px; text-align: justify; margin-bottom: 21px;
  }
  .closing { font-size: 20px; color: #222; margin-top: 22px; }
  .signature {
    font-family: "Great Vibes", cursive; font-size: 40px; color: var(--navy);
    line-height: 1.1; margin-top: 2px;
  }
  .contact {
    position: absolute; left: 66px; top: 1127px; list-style: none;
    font-size: 13px; line-height: 19px; color: #333;
  }
  .contact li { display: flex; align-items: center; gap: 5px; }
  .contact svg { width: 11px; height: 11px; fill: var(--red); }
</style>
</head>
<body>
<main class="letterhead">
  <header>
    <div class="brand">
      <span class="brand-mark"></span>
      <span class="brand-name">BRIGHTFIELD VENTURES INC.</span>
    </div>
    <div class="header-rule left"></div>
    <div class="header-web">www.<strong>brightfieldventures</strong>.example</div>
    <div class="header-rule right"></div>
  </header>

  <section class="letter-body">
    <div class="salutation">Dear Mr. Lorem,</div>
    <p>Lorem ipsum dolor sit amet, consectetuer adipiscing elit, sed diam nonummy nibh euismod tincidunt ut laoreet dolore magna aliquam erat volutpat. Ut wisi enim ad minim veniam, quis nostrud exerci tation ullamcorper suscipit lobortis nisl ut aliquip ex ea commodo consequat. Duis autem vel eum iriure dolor in hendiusto odio dignissim qui blandit praesent luptatum zzril delenit augue duis dolore te feugait nulla facilisi.</p>
    <p>Lorem ipsum dolor sit amet, consectetuer adipiscing elit, sed diam nonummy nibh euismod tincidunt ut laoreet dolore magna aliquam erat volutpat. Ut wisi enim ad minim veniam, quis nostrud exerci tation ullamcorper suscipit lobortis nisl ut aliquip ex ea commodo consequat. Duis autem vel eum iriure dolor in hendiusto odio dignissim qui blandit praesent luptatum zzril delenit augue duis dolore te feugait nulla facilisi.</p>
    <p>Lorem ipsum dolor sit amet, consectetuer adipiscing elit, sed diam nonummy nibh euismod tincidunt ut laoreet dolore magna aliquam erat volutpat. Ut wisi enim ad minim veniam, quis nostrud exerci tation ullamcorper suscipit lobortis nisl ut aliquip ex ea commodo consequat. Duis autem vel eum iriure dolor in hendiusto odio dignissim qui blandit praesent luptatum zzril delenit augue duis dolore te feugait nulla facilisi.</p>
    <div class="closing">Sincerely Your,</div>
    <div class="signature">Your Name</div>
  </section>

  <ul class="contact">
    <li><svg viewBox="0 0 12 12" aria-hidden="true"><path d="M3 1l2 2.5-1 1.2c.6 1.3 1.6 2.3 2.9 2.9l1.2-1L10.6 8.6 9.4 10.6C5 10.2 1.8 7 1.4 2.6z"/></svg>916-555-0187</li>
    <li><svg viewBox="0 0 12 12" aria-hidden="true"><path d="M1 3h10v7H1z M1 3l5 4 5-4" stroke="#fff" stroke-width=".8"/></svg>info@brightfieldventures.example</li>
    <li><svg viewBox="0 0 12 12" aria-hidden="true"><circle cx="6" cy="6" r="5"/></svg>www.brightfieldventures.example</li>
  </ul>
</main>
</body>
</html>
```